Small environmental consultancy needs a simple but professional web design

We are a boutique environmental consultancyand contracting business located in Margaret River in the South West of Western Australia.

We have two arms
1) Consulting which offers environmental planning, management and assessment services primarily to local government and the development industry.
2) Contracting which implements on site plans and on ground works primarily involving revegetation, bush regeneration and environmental weed control.

We need a simple yet professional web design within the wordpress platform that commmunicates professionalism, experience and technical expertise without appearing too corporate.

Something like this structure appeals:
http://fernquill.net.au/environment-services/
or
http://www.tallowbrookenvironmental.com.au/index.php

(without the image gallery function)

Target Market(s)

Local Government Officers deciding on tenders;
Developers, Engineers, Town Planning consultants looking for environmental expertise

Industry/Entity Type

Business

Number of Pages Required

5+ page

Font styles to use
Sans Serif

Colors
33a6d7
9bcb3c

Requirements
Must have
• Pages required include:
• Home
• Environmental Planning and Management
• Revegetation and Regeneration Implementation (This page can mirror the Environmental Planning and Management page exactly in structure but with different text and images)
• About Us (I think that this page can be relatively simple and generic)
• Contact (I think that this page can be very simple and generic)
Nice to have
• An ability to start out basic and quicikly establish a website presence and then build in additional drop downs and pages over time.
Should not have
• It does not need a photo gallery page;
• It does not need a major amount of space dedicated to social media and blogs etc as this is not currently particularly active area for us

```html
<!DOCTYPE html>
<html lang="en">
<head>
<meta charset="utf-8">
<title>Wandoo Ecoservices – Revegetation and Bush Regeneration</title>
<link rel="stylesheet" href="https://fonts.googleapis.com/css2?family=Open+Sans:wght@400;600;700&family=Raleway:wght@700;800&family=Teko:wght@400;500&display=swap">
<style>
  :root {
    --blue: #33a6d7;
    --blue-dark: #1f8cc4;
    --blue-line: #2a95c8;
    --green: #9bcb3c;
    --green-deep: #7ea126;
    --brown: #6b4a1f;
    --text: #555555;
    --heading-dark: #3d3d3d;
    --header-bg: #efefef;
    --footer-bg: #ebebeb;
    --rule: #d8d8d8;
    --field-border: #d6d6d6;
    --icon: #b5b5b5;
    --white: #ffffff;
  }
  * { box-sizing: border-box; margin: 0; padding: 0; }
  html, body { width: 1064px; height: 1200px; overflow: hidden; }
  body {
    font-family: "Open Sans", Arial, sans-serif;
    color: var(--text);
    background: var(--white);
    position: relative;
  }

  /* Header */
  .site-header {
    height: 155px;
    background: var(--header-bg);
    position: relative;
  }
  .brand {
    position: absolute;
    left: 65px;
    top: 42px;
    display: flex;
    align-items: center;
    gap: 16px;
  }
  .brand-mark {
    width: 58px; height: 58px;
    border-radius: 50%;
    background: var(--green);
  }
  .brand-name {
    font-family: "Open Sans", Arial, sans-serif;
    font-weight: 600;
    font-size: 31px;
    color: var(--brown);
    line-height: 1;
  }
  .brand-tagline {
    font-size: 12px;
    font-weight: 600;
    color: var(--brown);
    margin-top: 6px;
  }
  .call-us {
    position: absolute;
    right: 67px;
    top: 33px;
    text-align: left;
  }
  .call-us-label {
    font-weight: 700;
    font-size: 15px;
    color: #111;
    line-height: 18px;
  }
  .call-us-number {
    font-weight: 700;
    font-size: 25px;
    color: var(--blue);
    line-height: 28px;
  }
  .search {
    position: absolute;
    left: 809px;
    top: 94px;
    width: 188px;
    height: 23px;
    background: var(--white);
    border-radius: 2px;
    display: flex;
    align-items: center;
    justify-content: space-between;
    padding: 0 8px;
    font-size: 12px;
    color: #666;
  }

  /* Navigation */
  .main-nav {
    height: 39px;
    background: var(--blue);
    border-bottom: 3px solid var(--blue-line);
    display: flex;
    padding-left: 72px;
  }
  .main-nav a {
    font-family: "Raleway", Arial, sans-serif;
    font-weight: 800;
    font-size: 12.5px;
    color: var(--white);
    text-decoration: none;
    text-transform: uppercase;
    padding: 0 18px;
    line-height: 36px;
  }
  .main-nav a.is-current { background: var(--blue-dark); }

  /* Banner */
  .page-banner {
    height: 112px;
    background: linear-gradient(180deg, #3e4a2e 0%, #56663a 45%, #7d7a4e 70%, #5c6d39 100%);
  }

  /* Content */
  .content {
    padding: 28px 66px 0 65px;
  }
  .page-title {
    font-family: "Teko", "Arial Narrow", sans-serif;
    font-weight: 500;
    font-size: 40px;
    color: var(--green);
    text-transform: uppercase;
    line-height: 1;
    height: 48px;
  }
  .content p {
    font-size: 12.6px;
    line-height: 18.8px;
    margin-bottom: 18px;
  }
  .intro {
    display: flex;
    justify-content: space-between;
  }
  .intro-text { width: 534px; }
  .feature-photo {
    width: 374px;
    height: 253px;
    margin-top: 2px;
    background: linear-gradient(180deg, #3c4630 0%, #55643f 35%, #6f7a4c 55%, #4f8a63 80%, #5c7a45 100%);
  }
  .content .full { margin-top: -2px; }

  /* Footer */
  .site-footer {
    position: absolute;
    left: 0; top: 910px;
    width: 1064px; height: 290px;
    background: var(--footer-bg);
    border-top: 1px solid var(--rule);
  }
  .footer-heading {
    font-family: "Teko", "Arial Narrow", sans-serif;
    font-weight: 400;
    font-size: 20px;
    color: var(--heading-dark);
    text-transform: uppercase;
    line-height: 1;
  }
  .footer-col { position: absolute; top: 29px; }
  .footer-about { left: 65px; }
  .footer-site { left: 333px; }
  .footer-contact { left: 545px; }
  .footer-links { list-style: none; margin-top: 9px; }
  .footer-links li, .footer-site p {
    font-size: 12px;
    line-height: 18px;
    color: #444;
  }
  .footer-site p { margin-top: 9px; }
  .call-now { margin-top: 24px; }
  .call-now-number {
    display: flex;
    align-items: center;
    gap: 6px;
    font-family: "Teko", "Arial Narrow", sans-serif;
    font-weight: 500;
    font-size: 31px;
    color: var(--green);
    line-height: 1;
    margin-top: 6px;
  }
  .contact-form { position: relative; margin-top: 0; }
  .field {
    position: absolute;
    background: var(--white);
    border: 1px solid var(--field-border);
    font-size: 13px;
    color: #aaa;
    padding: 7px 11px;
  }
  .field svg { position: absolute; right: 8px; top: 7px; }
  .field-name { left: 0; top: 38px; width: 222px; height: 33px; }
  .field-email { left: 230px; top: 38px; width: 222px; height: 33px; }
  .field-message { left: 0; top: 79px; width: 452px; height: 65px; }
  .send-button {
    position: absolute;
    left: 0; top: 152px;
    width: 138px; height: 38px;
    background: linear-gradient(180deg, var(--green) 0%, var(--green-deep) 100%);
    border: 1px solid #6f8f1f;
    font-family: "Teko", "Arial Narrow", sans-serif;
    font-weight: 400;
    font-size: 20px;
    color: var(--white);
    text-transform: uppercase;
    line-height: 40px;
    text-align: center;
  }
  .footer-bottom {
    position: absolute;
    left: 65px; top: 246px;
    width: 956px;
    border-top: 1px solid var(--rule);
    padding-top: 12px;
    font-size: 12px;
    color: #444;
  }
</style>
</head>
<body>

<header class="site-header">
  <div class="brand">
    <span class="brand-mark"></span>
    <div>
      <div class="brand-name">Wandoo Ecoservices</div>
      <div class="brand-tagline">Environmental Assessment, Planning &amp; Management</div>
    </div>
  </div>
  <div class="call-us">
    <div class="call-us-label">Call Us</div>
    <div class="call-us-number">0400 382 617</div>
  </div>
  <div class="search">
    <span>Search</span>
    <svg width="14" height="14" viewBox="0 0 14 14" aria-hidden="true">
      <circle cx="6" cy="6" r="4.5" fill="none" stroke="#9a9a9a" stroke-width="1.8"/>
      <line x1="9.3" y1="9.3" x2="13" y2="13" stroke="#9a9a9a" stroke-width="2"/>
    </svg>
  </div>
</header>

<nav class="main-nav">
  <a href="#">Home</a>
  <a href="#">Environmental Planning and Management</a>
  <a href="#" class="is-current">Revegetation and Bush Regeneration</a>
  <a href="#">About Us</a>
  <a href="#">Contact</a>
</nav>

<div class="page-banner" role="img" aria-label="Banner photo of a revegetation site with rows of green tree guards in bushland"></div>

<main class="content">
  <h1 class="page-title">Revegetation and Bush Regeneration</h1>
  <div class="intro">
    <div class="intro-text">
      <p>Lorem ipsum dolor sit amet, consectetuer adipiscing elit, sed diam nonummy nibh euismod tincidunt ut laoreet dolore magna aliquam erat ullamcorper suscipit lobortis nisl ut aliquip ex ea commodo consequat. Lorem ipsum dolor sit amet, consectetuer adipiscing elit, sed diam nonummy nibh euismod tincidunt ut laoreet dolore magna aliquam erat volutpat. Ut wisi enim ad minim veniam, quis nostrud exerci tation ullamcorper suscipit lobortis nisl ut aliquip ex ea commodo consequat.Lorem ipsum dolor sit amet, consectetuer adipiscing elit, sed diam nonummy nibh euismod tincidunt ut laoreet dolore magna aliquam erat volutpat. Ut wisi enim ad minim veniam, quis nostrud exerci tation ullamcorper suscipit lobortis nisl ut aliquip ex ea commodo consequat.</p>
      <p>Lorem ipsum dolor sit amet, consectetuer adipiscing elit, sed diam nonummy nibh euismod tincidunt ut laoreet dolore magna aliquam erat volutpat. Ut wisi enim ad minim veniam, quis nostrud exerci tation ullamcorper suscipit lobortis nisl ut aliquip ex ea commodo consequat. Lorem ipsum dolor sit amet, consectetuer adipiscing elit, sed diam nonummy nibh euismod tincidunt ut laoreet dolore magna aliquam erat ullamcorper suscipit lobortis nisl ut aliquip ex ea commodo consequat.</p>
    </div>
    <div class="feature-photo" role="img" aria-label="Photo of seedlings in green tree guards planted in curving rows beneath eucalypt woodland"></div>
  </div>
  <p class="full">Lorem ipsum dolor sit amet, consectetuer adipiscing elit, sed diam nonummy nibh euismod tincidunt ut laoreet dolore magna aliquam erat ullamcorper suscipit lobortis nisl ut aliquip ex ea commodo consequat. Lorem ipsum dolor sit amet, consectetuer adipiscing elit, sed diam nonummy nibh euismod tincidunt ut laoreet dolore magna aliquam erat volutpat. Ut wisi enim ad minim veniam, quis nostrud exerci tation ullamcorper suscipit lobortis nisl ut aliquip ex ea commodo consequat.Lorem ipsum dolor sit amet, consectetuer adipiscing elit, sed diam nonummy nibh euismod tincidunt ut laoreet dolore magna aliquam erat volutpat. Ut wisi enim ad minim veniam, quis nostrud exerci tation ullamcorper suscipit lobortis nisl ut aliquip ex ea commodo consequat.</p>
  <p>Lorem ipsum dolor sit amet, consectetuer adipiscing elit, sed diam nonummy nibh euismod tincidunt ut laoreet dolore magna aliquam erat volutpat. Ut wisi enim ad minim veniam, quis nostrud exerci tation ullamcorper suscipit lobortis nisl ut aliquip ex ea commodo consequat. Lorem ipsum dolor sit amet, consectetuer adipiscing elit, sed diam nonummy nibh euismod tincidunt ut laoreet dolore magna aliquam erat ullamcorper suscipit lobortis nisl ut aliquip ex ea commodo consequat.</p>
</main>

<footer class="site-footer">
  <div class="footer-col footer-about">
    <h2 class="footer-heading">About</h2>
    <ul class="footer-links">
      <li>Environmental Planning and Management</li>
      <li>Revegetation and Bush Regeneration</li>
      <li>Contacts</li>
    </ul>
    <div class="call-now">
      <h2 class="footer-heading">Call us now:</h2>
      <div class="call-now-number">
        <svg width="20" height="20" viewBox="0 0 20 20" aria-hidden="true">
          <path d="M4 2 L7.5 2 L8.8 6 L6.6 7.6 C7.6 10 9.9 12.4 12.4 13.4 L14 11.2 L18 12.5 L18 16 C18 17.2 17 18 15.8 18 C8.3 17.5 2.5 11.7 2 4.2 C2 3 2.8 2 4 2 Z" fill="#555"/>
        </svg>
        <span>0400 382 617</span>
      </div>
    </div>
  </div>

  <div class="footer-col footer-site">
    <h2 class="footer-heading">Website</h2>
    <p>www.wandooecoservices.com.au</p>
  </div>

  <div class="footer-col footer-contact">
    <h2 class="footer-heading">Contact us</h2>
    <form class="contact-form">
      <div class="field field-name">Name
        <svg width="18" height="18" viewBox="0 0 18 18" aria-hidden="true">
          <circle cx="9" cy="5" r="4" fill="var(--icon)"/>
          <path d="M1 18 C1 12 4.5 10 9 10 C13.5 10 17 12 17 18 Z" fill="var(--icon)"/>
        </svg>
      </div>
      <div class="field field-email">E-mail
        <svg width="20" height="16" viewBox="0 0 20 16" aria-hidden="true">
          <rect x="0" y="1" width="20" height="14" rx="1.5" fill="var(--icon)"/>
          <path d="M1 2 L10 9 L19 2" fill="none" stroke="#fff" stroke-width="1.6"/>
        </svg>
      </div>
      <div class="field field-message">Message
        <svg width="20" height="17" viewBox="0 0 20 17" aria-hidden="true">
          <path d="M1 1 H19 V12 H8 L4 16 V12 H1 Z" fill="var(--icon)"/>
          <circle cx="6" cy="6.5" r="1.2" fill="#fff"/>
          <circle cx="10" cy="6.5" r="1.2" fill="#fff"/>
          <circle cx="14" cy="6.5" r="1.2" fill="#fff"/>
        </svg>
      </div>
      <div class="send-button">Send message</div>
    </form>
  </div>

  <div class="footer-bottom">© 2015 Wandoo Ecoservices. All Rights Reserved.</div>
</footer>

</body>
</html>
```